New Web Site Design - Tallow Ridge Communication Solutions

We are looking for a completely new web site design. Tallow Ridge Communication Solutions is a full service company providing PBX and IP/Cloud Based phone systems. We also sell and install video camera surveillance systems and provide low voltage cabling services (CAT5 and CAT3). We are looking for something professional looking. We want to be able to showcase our vendor partners as well as be able to show photos of some of the work we have done. We will also want to be able to post PDF brochures as well as make changes to the website ourselves.

Target Market(s)

Commercial

Industry/Entity Type

Communication

Coding

Coded - Design and coding required

Number of Pages Required

5+ page

Font styles to use
Sans Serif

Colors
0455a3

Requirements
Must have
• Ability to upload PDF brochures
• Professional look and feel
• Ability to upload and easily insert job photos
• Thinking it should have at least 6 pages: Main page, phone systems and services page, carrier services page, video surveillance systems and service page, low voltage cabling services page, contact us page

```html
<!DOCTYPE html>
<html lang="en">
<head>
<meta charset="utf-8">
<title>Tallow Ridge Communication Solutions – Phone Systems and Service</title>
<link href="https://fonts.googleapis.com/css2?family=Open+Sans:wght@400;600;700&display=swap" rel="stylesheet">
<style>
  :root{
    --brand:#0455a3;
    --nav-active:#5b95cf;
    --ink:#2b2b2b;
    --muted:#6b6b6b;
    --page:#ffffff;
    --footer:#3d4046;
    --footer-deep:#2c2e33;
    --footer-text:#c9ccd1;
    --footer-line:#565a61;
    --panel:#2a5f95;
    --panel-head:#3f3f44;
  }
  *{box-sizing:border-box;margin:0;padding:0}
  html,body{width:900px;height:1200px;overflow:hidden;background:var(--page)}
  body{font-family:"Open Sans",Arial,sans-serif;color:var(--ink);position:relative}

  /* header */
  .site-header{position:absolute;left:0;top:0;width:900px;height:117px;background:#fff}
  .brand-name{position:absolute;left:22px;top:30px;font-size:20px;font-weight:700;color:var(--brand);line-height:1.15;width:260px}
  .follow{position:absolute;right:22px;top:10px;display:flex;align-items:center;gap:6px;font-size:10px;color:var(--muted);white-space:nowrap}
  .follow .social{width:13px;height:13px;background:var(--brand)}
  .brochure-btn{position:absolute;left:512px;top:50px;width:176px;height:30px;background:var(--brand);color:#fff;font-size:11px;font-weight:600;display:flex;align-items:center;gap:8px;padding-left:10px;white-space:nowrap}
  .call{position:absolute;left:706px;top:46px;display:flex;align-items:center;gap:8px}
  .call-text small{display:block;font-size:10px;color:var(--muted)}
  .call-text strong{display:block;font-size:19px;color:var(--brand);font-weight:700;line-height:1.1;white-space:nowrap}

  /* nav */
  .main-nav{position:absolute;left:0;top:117px;width:900px;height:22px;background:var(--brand);display:flex;padding-left:14px}
  .main-nav a{color:#fff;text-decoration:none;font-size:10.5px;line-height:22px;padding:0 22px;white-space:nowrap}
  .main-nav a.active{background:var(--nav-active)}

  /* hero */
  .hero{position:absolute;left:0;top:139px;width:900px;height:282px;background:linear-gradient(120deg,#e9eaec 0%,#cfd1d4 45%,#8c8f94 75%,#d9dadc 100%)}

  /* content */
  .content{position:absolute;left:72px;top:440px;width:756px}
  .section-title{font-size:18px;font-weight:600;color:var(--ink)}
  .title-rule{width:44px;height:3px;background:var(--brand);margin:6px 0 10px}
  .intro{font-size:10px;line-height:1.55;color:var(--muted)}
  .service{position:absolute;left:0;width:756px;display:flex;gap:30px}
  .service-photo{flex:none;width:198px;height:124px;border:4px solid #e4e4e4;background:linear-gradient(135deg,#f3f3f3,#b9bcc0)}
  .service-body{width:528px}
  .service-body h3{font-size:11.5px;font-weight:700;color:var(--brand);margin:6px 0 6px}
  .service-body p{font-size:10px;line-height:1.6;color:var(--muted)}
  .service.one{top:100px}
  .service.two{top:280px}

  /* footer */
  .site-footer{position:absolute;left:0;top:895px;width:900px;height:275px;background:var(--footer)}
  .footer-heading{position:absolute;left:22px;top:14px;font-size:12px;color:#fff;font-weight:600}
  .footer-rule{position:absolute;left:0;top:36px;width:540px;height:1px;background:var(--footer-line)}
  .contact-list{position:absolute;left:28px;top:48px;list-style:none;width:290px}
  .contact-list li{display:flex;gap:10px;margin-bottom:9px;font-size:9.5px;line-height:1.4;color:var(--footer-text)}
  .contact-list svg{flex:none;margin-top:2px;width:13px}
  .contact-list b{color:#fff;font-weight:600}
  .footer-brand{position:absolute;left:340px;top:110px;width:180px;font-size:15px;font-weight:700;line-height:1.15;color:#dfe6ee;opacity:.3}

  .inquiry{position:absolute;left:598px;top:12px;width:246px;height:240px;background:var(--panel)}
  .inquiry-head{height:36px;background:var(--panel-head);color:#fff;font-size:14px;font-weight:600;display:flex;align-items:center;gap:10px;padding-left:12px}
  .inquiry-note{font-size:9.5px;color:#e6edf5;padding:10px 14px 8px}
  .field{margin:0 14px 6px;height:22px;background:rgba(255,255,255,.88);font-size:9.5px;color:#777;padding-left:8px;line-height:22px}
  .field.message{height:40px}
  .submit{margin:8px 14px 0;width:62px;height:22px;background:var(--brand);color:#fff;font-size:9.5px;font-weight:700;text-align:center;line-height:22px}

  .copyright{position:absolute;left:0;top:1170px;width:900px;height:30px;background:var(--footer-deep);color:#aeb2b8;font-size:9.5px;text-align:center;line-height:30px}
</style>
</head>
<body>

<header class="site-header">
  <div class="brand-name">Tallow Ridge<br>Communication Solutions</div>
  <div class="follow">Follow Us On <span class="social"></span><span class="social"></span><span class="social"></span></div>
  <div class="brochure-btn">
    <svg width="16" height="18" viewBox="0 0 16 18"><path d="M2 1h8l4 4v12H2z" fill="#fff"/><path d="M10 1v4h4" fill="none" stroke="#0455a3" stroke-width="1"/></svg>
    Download Our Brochure
  </div>
  <div class="call">
    <svg width="26" height="26" viewBox="0 0 24 24"><path d="M6.6 10.8a15 15 0 0 0 6.6 6.6l2.2-2.2a1 1 0 0 1 1-.25 11.4 11.4 0 0 0 3.6.57 1 1 0 0 1 1 1V20a1 1 0 0 1-1 1A17 17 0 0 1 3 4a1 1 0 0 1 1-1h3.5a1 1 0 0 1 1 1c0 1.25.2 2.45.57 3.6a1 1 0 0 1-.25 1z" fill="#0455a3"/></svg>
    <div class="call-text"><small>Call Us Today</small><strong>123-456-7890</strong></div>
  </div>
</header>

<nav class="main-nav">
  <a href="#">About Us</a>
  <a href="#" class="active">Phone Systems &amp; Service</a>
  <a href="#">Low Voltage Cabling Service</a>
  <a href="#">Carrier Services</a>
  <a href="#">Video Surveillance Systems Service</a>
</nav>

<div class="hero" role="img" aria-label="Photo of an office desk with a conference phone, desk telephone and notepad"></div>

<main class="content">
  <h1 class="section-title">Phone Systems and Service</h1>
  <div class="title-rule"></div>
  <p class="intro">We design, install and support business phone systems that keep your team connected. From small offices to multi-site operations, our technicians plan every detail, deliver on schedule and stay on call long after the system goes live.</p>

  <section class="service one">
    <div class="service-photo" role="img" aria-label="Photo of an IP business desk telephone"></div>
    <div class="service-body">
      <h3>Kestrel IP Business Telephone Systems</h3>
      <p>Our IP business telephone systems combine reliable desk handsets with flexible software features such as auto attendant, voicemail to email, call recording and mobile extensions. We size each system to your headcount and growth plans, handle the wiring and programming, and train your staff so the switch is smooth. Certified technicians provide ongoing maintenance and fast on-site repair whenever you need it.</p>
    </div>
  </section>

  <section class="service two">
    <div class="service-photo" role="img" aria-label="Photo of hosted VoIP devices: desk phone, laptop, tablet and smartphone"></div>
    <div class="service-body">
      <h3>Hosted/VoIP PBX Solutions</h3>
      <p>Move your phone system to the cloud and pay only for the lines you use. Hosted PBX service gives every employee a business number on desk phones, laptops and smartphones, with calls routed exactly the way you choose. We port your existing numbers, configure call flows and monitor quality around the clock, so your customers always reach the right person on the first ring.</p>
    </div>
  </section>
</main>

<footer class="site-footer">
  <h2 class="footer-heading">Contact Details</h2>
  <div class="footer-rule"></div>
  <ul class="contact-list">
    <li>
      <svg height="14" viewBox="0 0 12 14"><path d="M6 0a5 5 0 0 0-5 5c0 3.8 5 9 5 9s5-5.2 5-9a5 5 0 0 0-5-5zm0 7a2 2 0 1 1 0-4 2 2 0 0 1 0 4z" fill="#c9ccd1"/></svg>
      <div><b>Postal Address</b><br>Street Name, City Name State Zipcode</div>
    </li>
    <li>
      <svg height="12" viewBox="0 0 24 24"><path d="M6.6 10.8a15 15 0 0 0 6.6 6.6l2.2-2.2a1 1 0 0 1 1-.25 11.4 11.4 0 0 0 3.6.57 1 1 0 0 1 1 1V20a1 1 0 0 1-1 1A17 17 0 0 1 3 4a1 1 0 0 1 1-1h3.5a1 1 0 0 1 1 1c0 1.25.2 2.45.57 3.6a1 1 0 0 1-.25 1z" fill="#c9ccd1"/></svg>
      <div><b>Telephone</b><br>123-456-7890 &amp; Fax: 456-789-4560</div>
    </li>
    <li>
      <svg height="10" viewBox="0 0 13 10"><rect x=".5" y=".5" width="12" height="9" fill="none" stroke="#c9ccd1"/><path d="M.5.5l6 5 6-5" fill="none" stroke="#c9ccd1"/></svg>
      <div><b>Email</b><br>Information and Support: inquiry@tallowridge.com</div>
    </li>
    <li>
      <svg height="12" viewBox="0 0 12 12"><rect width="12" height="12" fill="#c9ccd1"/></svg>
      <div><b>Social Page</b><br>www.tallowridge.com/social</div>
    </li>
    <li>
      <svg height="12" viewBox="0 0 12 12"><rect width="12" height="12" fill="#c9ccd1"/></svg>
      <div><b>Photo Gallery</b><br>www.tallowridge.com/gallery</div>
    </li>
  </ul>

  <div class="footer-brand">Tallow Ridge<br>Communication Solutions</div>

  <form class="inquiry">
    <div class="inquiry-head">
      <svg width="18" height="16" viewBox="0 0 18 16"><path d="M2 1h14a1 1 0 0 1 1 1v9a1 1 0 0 1-1 1H7l-4 3v-3H2a1 1 0 0 1-1-1V2a1 1 0 0 1 1-1z" fill="#fff"/></svg>
      Quick Inquiry
    </div>
    <p class="inquiry-note">Send us a quick note and we will reply today.</p>
    <div class="field">Name</div>
    <div class="field">Email</div>
    <div class="field">Phone</div>
    <div class="field message">Message</div>
    <div class="submit">SUBMIT</div>
  </form>
</footer>

<div class="copyright">Copyright 2016. Tallow Ridge Communication Solutions. All Rights Reserved.</div>

</body>
</html>
```